Simple landing page for Brambles cookbook

I need a one page landingpage where customers can order the cookbook.
This is a cookbook of a collection of recipes from our deli that we used to run.
I need a landing page where customers can come and order the book. I also need it coded. I already have the domain through hostwell.
I can send the file of the book through wetransfer. It's too big to upload here. Just so you get the feel that I am looking for.
I attached a simple text as an introduction to the page. But I am open to any suggestions. I want it all to be about the experience that we are sharing the recipes with everybody and that it's for sale. The book is $29.99, shipping included.
Customers have to be able to click and buy the book from it.

Coding

Coded - Design and coding required

Number of Pages Required

1 page

Font styles to use
Sans Serif

Requirements
Must have
• Same colors as the cookbook

```html
<!DOCTYPE html>
<html lang="en">
<head>
<meta charset="utf-8">
<title>Brambles Cookbook</title>
<link rel="stylesheet" href="https://fonts.googleapis.com/css2?family=Fjalla+One&family=Quicksand:wght@500;600;700&display=swap">
<style>
:root{
  --brown:#4a2a17;
  --brown-dark:#3b2212;
  --pink:#c4185a;
  --pink-glow:rgba(214,40,110,.35);
  --green:#8fa82b;
  --green-dark:#6f8410;
  --green-pale:#e6eec4;
  --green-mist:#f3f7e4;
  --white:#ffffff;
  --wood:#6b4125;
}
*{box-sizing:border-box;margin:0;padding:0}
html,body{width:1200px;height:2483px;overflow:hidden}
body{position:relative;background:var(--white);font-family:"Quicksand",sans-serif;color:var(--brown)}
.abs{position:absolute}
.backdrop{position:absolute;left:0;top:0;width:1200px;height:2483px}
.brand{position:absolute;display:flex;align-items:center;gap:10px;font-family:"Quicksand",sans-serif;font-weight:700;color:var(--brown)}
.brand-dot{border-radius:50%;background:var(--green)}
.display{font-family:"Fjalla One",sans-serif;color:var(--brown);text-transform:uppercase;letter-spacing:1px}
.btn{position:absolute;display:flex;align-items:center;justify-content:center;width:146px;height:46px;border-radius:23px;background:var(--pink);color:var(--white);font-family:"Fjalla One",sans-serif;font-size:17px;letter-spacing:1.5px;text-decoration:none}
.price-badge{position:absolute;border-radius:50%;background:var(--pink);color:var(--white);display:flex;flex-direction:column;align-items:center;justify-content:center;box-shadow:0 0 60px 25px var(--pink-glow)}
.price{font-family:"Fjalla One",sans-serif;letter-spacing:1px}
.price sup{font-size:.5em;vertical-align:.35em}
.ship{display:flex;align-items:center;gap:6px;font-size:11px;line-height:1.1}
.placeholder{position:absolute}
.hero-title{position:absolute;left:145px;top:240px;font-size:43px;line-height:62px}
.story-card{position:absolute;left:145px;top:688px;width:910px;height:582px;border-radius:14px;overflow:hidden;display:flex;box-shadow:0 20px 60px rgba(0,0,0,.18)}
.story-photo{width:458px;height:100%;background:linear-gradient(160deg,#4f6a5e 0%,#3a3028 45%,#8b8f86 80%,#c9cbc4 100%)}
.story-text{flex:1;background:linear-gradient(160deg,#a2b63a 0%,var(--green) 50%,var(--green-dark) 100%);padding:72px 58px 0 57px;color:var(--white);font-size:12px;line-height:21px;letter-spacing:.3px}
.story-text p{margin-bottom:9px}
.story-name{font-family:"Fjalla One",sans-serif;font-size:22px;color:var(--brown);margin-right:6px}
.feature-card{position:absolute;left:613px;top:1562px;width:502px;height:207px;background:var(--white);border-radius:14px;box-shadow:0 10px 40px rgba(0,0,0,.08);text-align:center}
.feature-title{font-size:46px;line-height:50px;padding-top:12px}
.feature-sub{font-size:14px;line-height:19px;letter-spacing:1px;margin-top:6px}
.quote-box{position:absolute;left:145px;top:2170px;width:520px;height:208px;background:var(--white);border-left:5px solid var(--brown);border-bottom:5px solid var(--brown);border-top:3px solid #8a6a55;border-radius:14px;padding:44px 30px 0 30px;font-size:19px;line-height:30px;letter-spacing:1.3px}
.quote-mark{position:absolute;left:157px;top:2140px;width:60px;height:60px;border-radius:50%;background:var(--pink);color:var(--white);font-family:"Fjalla One",sans-serif;font-size:46px;line-height:72px;text-align:center}
.footer{position:absolute;left:0;top:2425px;width:1200px;height:58px;background:linear-gradient(180deg,var(--wood),var(--brown-dark));color:#f2e8de;font-size:15px;display:flex;align-items:center;justify-content:center;letter-spacing:.3px}
</style>
</head>
<body>

<svg class="backdrop" viewBox="0 0 1200 2483" aria-hidden="true">
  <defs>
    <linearGradient id="mist" x1="0" y1="0" x2="0" y2="1">
      <stop offset="0" stop-color="#f2f6e3"/><stop offset="1" stop-color="#ffffff"/>
    </linearGradient>
  </defs>
  <rect x="0" y="0" width="1200" height="620" fill="url(#mist)"/>
  <path d="M0 210 C260 120 520 110 760 170 C920 210 1080 300 1200 270 L1200 620 L0 620 Z" fill="#e4ecc2" opacity=".75"/>
  <path d="M0 390 C200 260 420 230 640 260 L640 620 L0 620 Z" fill="#f6f9ec"/>
  <path d="M78 222 C130 170 200 140 240 132 C180 160 120 195 78 222 Z" fill="#ffffff"/>
  <path d="M1050 290 C1110 270 1160 262 1200 260 L1200 300 C1150 290 1100 292 1050 290 Z" fill="#cfdd98"/>
  <path d="M0 1240 C120 1320 220 1370 380 1400 L0 1440 Z" fill="#e4ecc2" opacity=".8"/>
  <path d="M0 1400 C300 1470 520 1520 760 1490 C960 1460 1100 1420 1200 1390 L1200 1900 L0 1900 Z" fill="#eef3d8" opacity=".7"/>
  <path d="M1060 1600 C1120 1560 1170 1530 1200 1515 L1200 1540 C1160 1560 1110 1585 1060 1600 Z" fill="#ffffff"/>
</svg>

<div class="brand" style="left:148px;top:34px;font-size:38px">
  <span class="brand-dot" style="width:22px;height:22px"></span>Brambles
</div>

<h1 class="display hero-title">Your favourite Brambles<br>recipes, now available<br>in a cook book!</h1>
<a class="btn" href="#order" style="left:145px;top:453px">ORDER HERE</a>

<div class="placeholder" role="img" aria-label="Cookbook cover with a stacked sandwich photo" style="left:713px;top:60px;width:344px;height:500px;border-radius:4px 10px 10px 4px;background:linear-gradient(170deg,#e9eef3 0%,#f4efe8 30%,#c98a4b 55%,#7f9a4a 75%,#e6e6e6 100%);box-shadow:10px 10px 30px rgba(0,0,0,.15)"></div>

<div class="price-badge" style="left:642px;top:140px;width:140px;height:140px">
  <div class="price" style="font-size:38px"><sup>$</sup>29.99</div>
  <div class="ship">
    <svg width="26" height="16" viewBox="0 0 26 16" fill="none" stroke="#fff" stroke-width="1.5"><rect x="1" y="2" width="14" height="10"/><path d="M15 5h5l4 4v3h-9"/><circle cx="6" cy="13" r="2"/><circle cx="19" cy="13" r="2"/></svg>
    <span>Free<br>Shipping</span>
  </div>
</div>

<section class="story-card">
  <div class="story-photo" role="img" aria-label="Storefront of the former deli with its sign and shop windows"></div>
  <div class="story-text">
    <p><span class="story-name">Brambles</span>was a small Deli in Ashford Bay. After it opened its doors in 2010, it quickly turned into an iconic place, where people from all over came to enjoy one of the European inspired sandwiches. All the sauces were made in house and gave the sandwiches unique flavors. No wonder they turned into fan favourites.</p>
    <p>Now the recipes are available for everybody to use in this compilation of the most favourite menu items.</p>
    <p>Simple to follow instructions – it’s no rocket science! With common ingredients you will be able to whip those up in no time and enjoy for yourself or with friends.</p>
    <p>If you had the opportunity to visit Brambles in its days and enjoy one of the sandwich firsthand, now you can relive the glory days and make them at home!</p>
    <p>If you never had the chance to have a Brambles sandwich, you can still get a taste of what the hype was all about.</p>
  </div>
</section>
<a class="btn" href="#order" style="left:651px;top:1160px">ORDER HERE</a>
<div class="placeholder" role="img" aria-label="Illustrated green pickle" style="left:915px;top:1150px;width:200px;height:175px;border-radius:50% 50% 50% 50% / 60% 60% 40% 40%;background:linear-gradient(150deg,#a9cf3a,#6f9a1f);transform:rotate(-35deg)"></div>

<div class="placeholder" role="img" aria-label="Open cookbook showing sandwich recipe pages beside the cover" style="left:0;top:1450px;width:680px;height:440px;border-radius:8px;background:linear-gradient(150deg,#eef0f2 0%,#d9b48a 40%,#f2f2f2 65%,#cfd6c0 100%);opacity:.9;transform:skewY(-12deg)"></div>

<div class="price-badge" style="left:811px;top:1443px;width:108px;height:108px">
  <div class="price" style="font-size:30px"><sup>$</sup>29.99</div>
  <div class="ship" style="font-size:9px">
    <svg width="20" height="13" viewBox="0 0 26 16" fill="none" stroke="#fff" stroke-width="1.5"><rect x="1" y="2" width="14" height="10"/><path d="M15 5h5l4 4v3h-9"/><circle cx="6" cy="13" r="2"/><circle cx="19" cy="13" r="2"/></svg>
    <span>Free<br>Shipping</span>
  </div>
</div>

<section class="feature-card">
  <h2 class="display feature-title">Favorite recipes<br>in one book</h2>
  <p class="feature-sub">We Truly Hope You Will Enjoy Making These<br>Sandwiches Just As Much As We Did.</p>
</section>
<a class="btn" id="order" href="#order" style="left:792px;top:1746px">ORDER HERE</a>

<div class="placeholder" role="img" aria-label="Close-up photo of a toasted sandwich with melted cheese, tomato and herbs" style="left:330px;top:1930px;width:870px;height:495px;background:radial-gradient(ellipse at 65% 55%,#e9e1cc 0%,#cfc3a0 35%,#9e9a6e 60%,rgba(255,255,255,0) 80%)"></div>

<div class="brand" style="left:153px;top:2015px;font-size:60px">
  Brambles<span class="brand-dot" style="width:26px;height:26px"></span>
</div>

<blockquote class="quote-box">We can’t open another BRAMBLES, but we can offer you this collection of our recipes for you to try out at home with your family and friends.</blockquote>
<div class="quote-mark" aria-hidden="true">“</div>

<footer class="footer">Copyright 2022. Mara Linden | All Rights Reserved</footer>

</body>
</html>
```